Advertisement Design Project

I would like to have some advertisement ideas to promote my business. Our company provides credit repair, tax preparation, notary service, ledger preparation (for small businesses and independent contractors) tax restoration (help people with liens, levy, garnishments, etc. by negotiating with the NTB in these matters)

The name of our company is Vel Marin Financing
Our "BrivoMendup" program focuses on tax preparation, restoration, and credit repair.
Our "Brisk Start" program prepares ledgers for small business and independent contractors by preparing monthly ledgers so that at tax season they are not having to look everywhere for their receipts in order to get all deductions due to them during the tax season.

We need something that is catchy and will gain attention

attached is our logo. Our slogan is "Happiness, Restored!"

Thank you!

Target Market(s)

The financially distressed
Small business owners
Independent contractors
businesses that rely on credit worthy clients to do business with

Industry/Entity Type

Small Business

Requirements
Must have
• great pictures
nice layout

```html
<!DOCTYPE html>
<html lang="en">
<head>
<meta charset="utf-8">
<title>Vel Marin Financing – Happiness, Restored!</title>
<link rel="stylesheet" href="https://fonts.googleapis.com/css2?family=Cinzel:wght@400;600&family=Roboto:wght@300;400;700;900&family=Roboto+Condensed:wght@700&display=swap">
<style>
  :root{
    --navy:#173f6b;
    --navy-deep:#0f3557;
    --band-blue:#3f78ad;
    --ink:#1e1e1e;
    --body:#333a40;
    --red:#d9262b;
    --orange:#f08a1c;
    --silver:#c9ced3;
    --paper:#ffffff;
    --stage:#ece8e2;
  }
  *{margin:0;padding:0;box-sizing:border-box}
  html,body{width:953px;height:1200px;overflow:hidden;background:var(--stage)}
  .flyer{position:absolute;left:61px;top:67px;width:830px;height:1064px;background:var(--paper);overflow:hidden;font-family:"Roboto",Arial,sans-serif}
  .top-tint{position:absolute;left:0;top:0;width:830px;height:300px;background:linear-gradient(#f1f3f5,#ffffff)}

  .brand-box{position:absolute;left:40px;top:4px;width:186px;height:216px;background:var(--navy);border:3px solid #fff;outline:1px solid #d6dbe0;display:flex;flex-direction:column;align-items:center;justify-content:center;gap:16px}
  .brand-box .mark{width:34px;height:34px;border:2px solid #fff}
  .brand-box .name{font-family:"Cinzel",Georgia,serif;color:#fff;font-size:15px;text-align:center;line-height:1.2}

  .slogan-band{position:absolute;left:301px;top:100px;width:529px;height:120px}
  .slogan-band svg{position:absolute;inset:0}
  .slogan{position:absolute;right:16px;top:8px;text-align:right;font-family:"Cinzel",Georgia,serif;font-weight:600;color:#fff;font-size:47px;line-height:1.1;letter-spacing:2px}

  .offer-lead{position:absolute;left:36px;top:262px;font-weight:900;font-size:39px;letter-spacing:3px;color:var(--ink);line-height:1.2}
  .offer-title{position:absolute;left:36px;top:318px;font-weight:900;font-size:56px;line-height:1;color:var(--navy)}

  .copy{position:absolute;left:37px;top:466px;width:313px;font-size:11.3px;line-height:14.6px;color:var(--body);text-align:justify}
  .copy p{margin-bottom:10px}

  .photo{position:absolute;left:600px;top:560px;width:230px;height:340px;background:linear-gradient(160deg,#ffffff 0%,#eef0f2 30%,#c6cbd1 70%,#eceef0 100%)}
  .coins{position:absolute;left:358px;top:590px;width:196px;height:200px;border-radius:50% / 16%;background:linear-gradient(180deg,#f2f3f4,#c4c8cc 70%,#ead08a)}
  .arrow-art{position:absolute;left:0;top:790px;width:400px;height:130px;background:linear-gradient(30deg,rgba(210,30,35,.8),rgba(235,80,80,.35) 55%,rgba(255,255,255,0) 85%)}

  .provide-pill{position:absolute;left:493px;top:277px;width:337px;height:53px;border-radius:27px 0 0 27px;background:linear-gradient(#ffffff,#dcdfe3);border-top:3px solid var(--band-blue);box-shadow:0 2px 3px rgba(0,0,0,.2);font-weight:300;font-size:37px;letter-spacing:3px;color:var(--ink);padding-left:58px;line-height:46px}

  .services{position:absolute;right:58px;top:352px;list-style:none;text-align:right}
  .services li{font-family:"Roboto Condensed","Arial Narrow",sans-serif;font-weight:700;font-size:25px;color:var(--ink);height:43px;display:flex;align-items:center;justify-content:flex-end;gap:10px}
  .services svg{width:28px;height:28px}

  .program-mark{position:absolute;left:560px;top:944px;display:flex;align-items:center;gap:10px;font-weight:700;font-size:30px;color:var(--navy)}
  .program-mark .sq{width:18px;height:18px;background:var(--navy)}

  .contact{position:absolute;left:40px;top:944px;font-size:11.8px;line-height:1.75;color:var(--ink);font-style:normal}
  .contact strong{font-weight:700}

  .footer{position:absolute;left:0;top:996px;width:830px;height:68px}
  .footer svg{position:absolute;inset:0}
  .url{position:absolute;left:36px;top:1010px;font-weight:700;font-size:27px;letter-spacing:2px;color:#fff}
</style>
</head>
<body>
<main class="flyer">
  <div class="top-tint"></div>

  <div class="brand-box">
    <span class="mark"></span>
    <span class="name">Vel Marin Financing</span>
  </div>

  <div class="slogan-band">
    <svg viewBox="0 0 529 120" width="529" height="120">
      <path d="M60 0 H529 V120 H0 C25 120 30 0 60 0 Z" fill="var(--band-blue)"/>
    </svg>
    <div class="slogan">HAPPINESS,<br>RESTORED!</div>
  </div>

  <div class="photo" role="img" aria-label="Photo of a businessman in a suit using a calculator at a desk"></div>
  <div class="arrow-art" role="img" aria-label="Illustration of a red ribbon arrow rising upward"></div>
  <div class="coins" role="img" aria-label="Illustration of a stack of silver and gold coins"></div>

  <h2 class="offer-lead">We Offering...</h2>
  <h1 class="offer-title">BrivoMendup<br>program</h1>

  <div class="copy">
    <p>Our BrivoMendup program enables our clients to find solutions for financial situations that are keeping them from achieving their goal of ownership and living a fulfilled life.</p>
    <p>Our BrivoMendup program will help you settle your debt to the NTB, alleviate your credit burden with your creditors, and assist with some light bookkeeping that will make things easier during the tax season for small businesses and independent contractors.</p>
    <p>There is no reason to live a stressfull life when a solution is being offered to you. Our fees are reasonable and our service is fantastic. Our goal is to build a cliente base that will be happy with our service, and appreciate our company culture and at the same time become customers for life.</p>
    <p>Please feel free to browse our website for tools helpful to your needs.</p>
  </div>

  <div class="provide-pill">we provide</div>

  <ul class="services">
    <li><svg viewBox="0 0 28 28"><circle cx="13" cy="15" r="11" fill="none" stroke="var(--navy)" stroke-width="2.5"/><path d="M7 14 L12 20 L25 3" fill="none" stroke="var(--red)" stroke-width="3.5" stroke-linecap="round" stroke-linejoin="round"/></svg>TAX PREPARATION</li>
    <li><svg viewBox="0 0 28 28"><circle cx="13" cy="15" r="11" fill="none" stroke="var(--navy)" stroke-width="2.5"/><path d="M7 14 L12 20 L25 3" fill="none" stroke="var(--red)" stroke-width="3.5" stroke-linecap="round" stroke-linejoin="round"/></svg>RESTORATION</li>
    <li><svg viewBox="0 0 28 28"><circle cx="13" cy="15" r="11" fill="none" stroke="var(--navy)" stroke-width="2.5"/><path d="M7 14 L12 20 L25 3" fill="none" stroke="var(--red)" stroke-width="3.5" stroke-linecap="round" stroke-linejoin="round"/></svg>CREDIT REPAIR</li>
    <li><svg viewBox="0 0 28 28"><circle cx="13" cy="15" r="11" fill="none" stroke="var(--navy)" stroke-width="2.5"/><path d="M7 14 L12 20 L25 3" fill="none" stroke="var(--red)" stroke-width="3.5" stroke-linecap="round" stroke-linejoin="round"/></svg>LEDGER PREPARATION</li>
    <li><svg viewBox="0 0 28 28"><circle cx="13" cy="15" r="11" fill="none" stroke="var(--navy)" stroke-width="2.5"/><path d="M7 14 L12 20 L25 3" fill="none" stroke="var(--red)" stroke-width="3.5" stroke-linecap="round" stroke-linejoin="round"/></svg>TAX RESTORATION</li>
  </ul>

  <div class="program-mark"><span class="sq"></span>BrivoMendup</div>

  <address class="contact">
    <strong>Vel Marin Financing - Happiness, Restored!</strong><br>
    4810 Calloway Ave. # B7, Fernhill, TX 77561, E: info@velmarinfinancing.com
  </address>

  <div class="footer">
    <svg viewBox="0 0 830 68" width="830" height="68">
      <path d="M480 0 H830 V68 H430 Z" fill="var(--orange)"/>
      <path d="M0 0 H520 L468 68 H0 Z" fill="var(--silver)"/>
      <path d="M0 4 H508 L460 68 H0 Z" fill="var(--navy-deep)"/>
    </svg>
  </div>
  <div class="url">www.velmarinfinancing.com</div>
</main>
</body>
</html>
```